Sunset Harbor Living Web Page

We need a web page design that has two intro pages - first being a 'home page', then a link to the second page that has the 'content tabs' and a 'call to action' (see below).

The business helps people that wish to retire to S.E.Asia (Thailand, Malaysia, Indonesia,The Philippines etc) - to enjoy the lifestyle and the remaining years of their lives. What attracts S.E.Asia to many people is the lower cost, the atmoshpere and beauty of the tropics and the vibrancy of the various countries.

People that are wishing to make the most of their retirement and are adventurous at a great bargain compared to the cost of their own countries will be interested.

We help them achieve this - visa, financials (tax, gov't payments etc), introduce them to the right people for property, clubs, retirement facilities, insurance and so forth.

Therefore we are providing an extremely wide ranging service and this site will provide broad but general information only - with a call to action to come and see us for more specific information and how we can help them specifically.

This site will be predominantly for travel and lifestyle, it will be linked with another financial services (financial planning) site later down the track.

The colour scheme is dark green and blue - as per the attached logo design. Photos and background just think lifestyle and S.E.Asia - beaches/mountains/water/recreational activities for retirees.

Target market is mostly those coming up to retirement to those that are already retired. But we also expect to have some interest with younger people that would like to find out more and plan for the future. So a broad age group but I would say mostly 40-70 yrs old.

On the first (Home) page we would like our company name 'Sunset Harbor Living', our logo (which will be on all pages) and a statement such as: “Imagine a retirement where your dreams are brought to life, and you have never felt more alive. Let us show you how”. Then a link to the second page.

We would like an uncluttered site. On the second (contents) page the tabs would be:

- Visa
- Property
- Financials
- Travel
- Insurance & Healthcare
- Medical Tourism
- Cost of living
- Weekly Blogs and articles
- Sunset Harbor Living story

We would also like a call to action on the second page - asking them to leave their contact details if they wish to learn more or sign up to our weekly newsletter/blog.

We are open to suggestions and your imaginations.

Thank you
Malcolm

Font styles to use
Serif
Script

Colors
0255a3
3377b5
00a990
9bcb3c
abd036
33b8a4
85abd2
cadf82
86cfc6

Requirements
Must have
• I have been asked by the web designer to receive a 'Web Font' so that we can 'get off of Zentrofy'. Hope that makes sense.

```html
<!DOCTYPE html>
<html lang="en">
<head>
<meta charset="utf-8">
<title>Sunset Harbor Living</title>
<link href="https://fonts.googleapis.com/css2?family=Open+Sans:wght@400;600;700&family=Raleway:wght@500;600;700&display=swap" rel="stylesheet">
<style>
:root{
  --blue:#0255a3;
  --blue-mid:#3377b5;
  --blue-footer:#3a76b8;
  --teal:#00a990;
  --teal-light:#33b8a4;
  --green:#9bcb3c;
  --green-2:#7fb632;
  --text:#333;
  --muted:#777;
  --link:#1a8fd0;
  --star:#f29a1f;
  --red:#e0442b;
  --topbar:#eeeeee;
  --dark:#1c1c1c;
}
*{box-sizing:border-box;margin:0;padding:0}
html,body{width:1200px;height:2761px;overflow:hidden}
body{position:relative;font-family:"Open Sans",Arial,sans-serif;color:var(--text);background:#fff}
h2,h3,h4{font-family:"Raleway","Open Sans",sans-serif;font-weight:600}
.accent{color:var(--teal)}

/* header */
.topbar{position:absolute;left:337px;top:0;width:863px;height:44px;background:var(--topbar);font-size:12.5px;color:#555}
.topbar .item{position:absolute;top:0;height:44px;display:flex;align-items:center;gap:7px;white-space:nowrap}
.topbar svg{fill:var(--teal)}
.signup{position:absolute;left:568px;top:8px;width:74px;height:28px;border:1px solid var(--blue-mid);border-radius:3px;font-size:13px;color:var(--blue);display:flex;align-items:center;justify-content:center;background:#fff}
.social-top{position:absolute;left:662px;top:14px;display:flex;gap:20px}
.social-top span{width:15px;height:15px;border-radius:50%;background:#333;display:block}
.brand{position:absolute;left:96px;top:30px;width:200px;text-align:center}
.brand .mark{width:62px;height:62px;border-radius:50%;background:var(--teal);margin:0 auto 6px}
.brand .name{font-family:"Open Sans",sans-serif;font-weight:700;font-size:19px;color:var(--blue);line-height:1.1}
.nav{position:absolute;top:94px;left:347px;display:flex;font-size:14px;font-family:"Open Sans",sans-serif;color:#222}
.nav a{text-decoration:none;color:#222;margin-right:35px;letter-spacing:.2px}
.nav a.active{color:var(--blue-mid)}

/* hero */
.hero{position:absolute;left:0;top:151px;width:1200px;height:578px;background:linear-gradient(180deg,#6fb3e4 0%,#a6d6ee 22%,#3c8a3a 40%,#2f9bc8 60%,#1d76b3 100%)}
.hero-title{position:absolute;right:62px;top:224px;color:#fff;text-shadow:0 2px 4px rgba(0,0,0,.35);white-space:nowrap}
.hero-title h1{font-family:"Open Sans",sans-serif;font-weight:700;font-size:46px;line-height:1}
.hero-title p{font-family:"Open Sans",sans-serif;font-weight:700;font-size:23px;margin-top:6px}
.arrow-hero{position:absolute;top:244px}
.search{position:absolute;left:88px;top:392px;width:1025px;height:169px;background:rgba(20,20,20,.82)}
.search h3{color:#fff;text-align:center;font-size:21px;font-weight:500;letter-spacing:1px;margin-top:22px;font-family:"Open Sans",sans-serif}
.search .inner{position:absolute;left:17px;top:62px;width:990px;height:100px;background:#1e1e1e}
.field{position:absolute;top:0}
.field label{display:block;color:#fff;font-size:12px;margin:18px 0 9px 0}
.field .box{height:48px;background:#fff;border-radius:3px;position:relative}
.search-btn{position:absolute;left:838px;top:44px;width:134px;height:50px;background:var(--link);color:#fff;font-size:15px;display:flex;align-items:center;justify-content:center;border-radius:2px;font-weight:600}

/* welcome */
.welcome{position:absolute;left:0;top:780px;width:1200px;text-align:center}
.welcome h2{font-size:24px;font-weight:500;color:#222;letter-spacing:.5px}
.welcome p{width:1090px;margin:12px auto 0;font-size:13.5px;line-height:21px;color:#555}

/* section heads */
.sec-head{position:absolute;font-size:21px;font-weight:600;color:#222;letter-spacing:.5px}
.pager{position:absolute}

/* property */
.prop{position:absolute;top:1003px;width:324px}
.prop .photo{height:215px}
.prop h4{font-family:"Open Sans",sans-serif;font-weight:600;font-size:15.5px;margin-top:15px;color:#333}
.rating{display:flex;align-items:center;margin-top:12px}
.rating .reviews{color:var(--red);font-size:12px;margin-left:14px}
.prop p{font-size:12px;line-height:20px;color:#777;margin-top:14px}
.more{font-size:11.5px;color:var(--link);margin-top:10px;display:block}

/* services band */
.services{position:absolute;left:0;top:1443px;width:1200px;height:336px;background:linear-gradient(180deg,#a4d04a,#7ab52e)}
.svc{position:absolute;top:60px;width:260px;text-align:center;color:#fff}
.svc .circle{width:110px;height:110px;border-radius:50%;background:#fff;margin:0 auto;display:flex;align-items:center;justify-content:center;box-shadow:0 0 0 6px rgba(255,255,255,.25)}
.svc h4{font-family:"Open Sans",sans-serif;font-size:15px;font-weight:600;margin-top:26px;letter-spacing:.3px}
.svc p{font-size:11px;line-height:19px;margin:10px auto 0;width:225px}

/* places */
.place{position:absolute;top:1882px;width:249px;height:219px;border:1px solid #ccc;background:#fff}
.place .photo{height:167px}
.place .cap{position:absolute;left:10px;top:178px;font-size:13px;color:#333}
.place .mini{position:absolute;left:10px;top:199px}
.place .chev{position:absolute;right:10px;top:178px}

/* blogs */
.blogs{position:absolute;left:0;top:2166px;width:1200px;height:287px;background:#f1f1f1}
.blog-photo{position:absolute;top:101px;width:215px;height:147px;border:4px solid #fff;box-shadow:0 0 3px rgba(0,0,0,.2)}
.blog-text{position:absolute;top:104px;width:270px}
.blog-text h4{font-family:"Open Sans",sans-serif;font-size:13px;font-weight:700;color:#222}
.blog-text .date{font-size:10.5px;color:var(--link);margin-top:6px}
.blog-text p{font-size:10px;line-height:18px;color:#777;margin-top:6px}

/* footer */
.footer{position:absolute;left:0;top:2453px;width:1200px;height:239px;background:var(--blue-footer);color:#fff}
.fcol{position:absolute;top:44px}
.fcol h4{font-family:"Open Sans",sans-serif;font-size:16.5px;font-weight:500;letter-spacing:.5px}
.fcol p,.fcol li{font-size:12.5px;line-height:19px}
.fcol ul{list-style:none}
.email-box{width:215px;height:31px;background:#fff;color:#444;font-size:12px;display:flex;align-items:center;padding-left:10px;margin-top:18px}
.sub-btn{display:inline-block;margin-top:12px;background:#111;color:#fff;font-size:11px;padding:7px 10px;border-radius:3px;letter-spacing:.5px}
.tweet{display:flex;gap:10px;margin-top:18px}
.follow li{display:flex;align-items:center;gap:14px;margin-top:12px}
.follow .ring{width:30px;height:30px;border-radius:50%;border:1.5px solid #fff;display:flex;align-items:center;justify-content:center}
.follow .ring span{width:10px;height:10px;background:#fff;border-radius:50%}
.copyright{position:absolute;left:0;top:2692px;width:1200px;height:69px;background:var(--dark);color:#fff;font-size:12px;text-align:center;line-height:69px}
</style>
</head>
<body>

<svg width="0" height="0" style="position:absolute">
  <defs>
    <polygon id="star" points="10,1 12.6,7 19,7.3 14,11.4 15.7,18 10,14.3 4.3,18 6,11.4 1,7.3 7.4,7"/>
    <polyline id="chev-r" points="2,1 9,8 2,15" fill="none" stroke-width="2.2"/>
    <polyline id="chev-l" points="9,1 2,8 9,15" fill="none" stroke-width="2.2"/>
  </defs>
</svg>

<header>
  <div class="brand">
    <div class="mark"></div>
    <div class="name">Sunset Harbor Living</div>
  </div>
  <div class="topbar">
    <div class="item" style="left:36px"><svg width="13" height="13" viewBox="0 0 24 24"><path d="M6.6 10.8a15 15 0 0 0 6.6 6.6l2.2-2.2c.3-.3.7-.4 1-.2 1.1.4 2.3.6 3.6.6.6 0 1 .4 1 1V20c0 .6-.4 1-1 1C10.6 21 3 13.4 3 4c0-.6.4-1 1-1h3.5c.6 0 1 .4 1 1 0 1.3.2 2.5.6 3.6.1.3 0 .7-.2 1z"/></svg>+44 (0)20 - 5550148</div>
    <div class="item" style="left:190px"><svg width="12" height="14" viewBox="0 0 24 28"><path d="M12 0a9 9 0 0 0-9 9c0 7 9 19 9 19s9-12 9-19a9 9 0 0 0-9-9zm0 12.5A3.5 3.5 0 1 1 12 5.5a3.5 3.5 0 0 1 0 7z"/></svg>Find our Address</div>
    <div class="item" style="left:328px"><svg width="15" height="12" viewBox="0 0 24 18"><path d="M0 0h24v18H0z" fill="none" stroke="#00a990" stroke-width="3"/><path d="M1 1l11 9 11-9" fill="none" stroke="#00a990" stroke-width="2.5"/></svg>info@sunsetharborliving.com</div>
    <div class="signup">Sign up</div>
    <div class="social-top"><span></span><span></span><span></span><span></span></div>
  </div>
  <nav class="nav">
    <a class="active">HOME</a><a>VISA</a><a>PROPERTY</a><a>FINANCIALS</a><a>TRAVEL</a><a>COST OF LIVING</a><a>BLOG</a><a>CONTACT US</a>
  </nav>
</header>

<section class="hero" role="img" aria-label="Tropical resort pool with white sun loungers, umbrellas and palm trees">
  <svg class="arrow-hero" style="left:38px" width="30" height="60" viewBox="0 0 30 60"><polyline points="28,2 2,30 28,58" fill="none" stroke="#fff" stroke-width="2"/></svg>
  <svg class="arrow-hero" style="left:1132px" width="30" height="60" viewBox="0 0 30 60"><polyline points="2,2 28,30 2,58" fill="none" stroke="#fff" stroke-width="2"/></svg>
  <div class="hero-title">
    <h1>Sunset Harbor Living</h1>
    <p>Neque porro quisquam est qui</p>
  </div>
  <form class="search">
    <h3>WHERE DO YOU WANT TO STAY?</h3>
    <div class="inner">
      <div class="field" style="left:15px;width:373px"><label>Destination/Hotel Name</label><div class="box"></div></div>
      <div class="field" style="left:407px;width:132px"><label>Check-in Date</label><div class="box"><svg style="position:absolute;right:12px;top:17px" width="14" height="14" viewBox="0 0 14 14"><rect x="1" y="2" width="12" height="11" fill="none" stroke="#555"/><path d="M1 5h12M4 0v3M10 0v3" stroke="#555"/></svg></div></div>
      <div class="field" style="left:550px;width:133px"><label>Check-out Date</label><div class="box"><svg style="position:absolute;right:12px;top:17px" width="14" height="14" viewBox="0 0 14 14"><rect x="1" y="2" width="12" height="11" fill="none" stroke="#555"/><path d="M1 5h12M4 0v3M10 0v3" stroke="#555"/></svg></div></div>
      <div class="field" style="left:694px;width:134px"><label>Max Budgets</label><div class="box" style="font-size:11px;color:#555;padding:17px 0 0 14px">0 ADULT<svg style="position:absolute;right:14px;top:21px" width="10" height="6"><polygon points="0,0 10,0 5,6" fill="#555"/></svg></div></div>
      <div class="search-btn">SEARCH</div>
    </div>
  </form>
</section>

<section class="welcome">
  <h2>WELCOME TO <span class="accent">SUNSET HARBOR LIVING</span></h2>
  <p>Lorem Ipsum has been the industry's standard dummy text ever since the 1500s, when an unknown printer took a galley of type and scrambled it to make a type specimen book. It has survived not only five centuries, but also the leap into electronic typesetting, remaining essentially unchanged. It was popularised in the 1960s with the release of Letraset sheets containing Lorem Ipsum passages, and more recently with desktop</p>
</section>

<h2 class="sec-head" style="left:94px;top:958px">OUR <span class="accent">PROPERTY</span></h2>
<svg class="pager" style="left:1075px;top:957px" width="32" height="18" viewBox="0 0 32 18"><use href="#chev-l" stroke="#222"/><use href="#chev-r" x="20" stroke="#222"/></svg>

<article class="prop" style="left:94px">
  <div class="photo" role="img" aria-label="Ancient temple ruins with an elephant ride on green lawns" style="background:linear-gradient(180deg,#7fb6e6,#b8d3e6 45%,#6f9a3c 70%,#4f7d25)"></div>
  <h4>Neque porro quisquam est</h4>
  <div class="rating"><svg width="110" height="20" viewBox="0 0 110 20"><use href="#star" fill="var(--star)"/><use href="#star" x="22" fill="var(--star)"/><use href="#star" x="44" fill="var(--star)"/><use href="#star" x="66" fill="var(--star)"/><use href="#star" x="88" fill="#f6c37c"/></svg><span class="reviews">422 Reviews</span></div>
  <p>Lorem Ipsum has been the industry's standard dummy text ever since the 1500s, when an unknown printer took a galley of type and scrambled it to make</p>
  <a class="more">Read More &gt;&gt;</a>
</article>
<article class="prop" style="left:442px">
  <div class="photo" role="img" aria-label="City skyline with twin towers under a blue sky" style="background:linear-gradient(180deg,#4d8fd4,#a9c8e8 45%,#8f9aa3 70%,#556270)"></div>
  <h4>Neque porro quisquam est</h4>
  <div class="rating"><svg width="110" height="20" viewBox="0 0 110 20"><use href="#star" fill="var(--star)"/><use href="#star" x="22" fill="var(--star)"/><use href="#star" x="44" fill="var(--star)"/><use href="#star" x="66" fill="var(--star)"/><use href="#star" x="88" fill="#f6c37c"/></svg><span class="reviews">422 Reviews</span></div>
  <p>Lorem Ipsum has been the industry's standard dummy text ever since the 1500s, when an unknown printer took a galley of type and scrambled it to make</p>
  <a class="more">Read More &gt;&gt;</a>
</article>
<article class="prop" style="left:788px">
  <div class="photo" role="img" aria-label="Water temple with tiered roofs on a lake and mountains behind" style="background:linear-gradient(180deg,#c9d3dc,#9aa9b4 40%,#5d5a4b 65%,#7d8f97)"></div>
  <h4>Neque porro quisquam est</h4>
  <div class="rating"><svg width="110" height="20" viewBox="0 0 110 20"><use href="#star" fill="var(--star)"/><use href="#star" x="22" fill="var(--star)"/><use href="#star" x="44" fill="var(--star)"/><use href="#star" x="66" fill="var(--star)"/><use href="#star" x="88" fill="#f6c37c"/></svg><span class="reviews">422 Reviews</span></div>
  <p>Lorem Ipsum has been the industry's standard dummy text ever since the 1500s, when an unknown printer took a galley of type and scrambled it to make</p>
  <a class="more">Read More &gt;&gt;</a>
</article>

<section class="services">
  <div class="svc" style="left:72px">
    <div class="circle"><svg width="44" height="48" viewBox="0 0 44 48"><path d="M6 4h18l8 8v26H6z" fill="#8cc13a"/><path d="M14 12h18l8 8v26H14z" fill="#8cc13a" stroke="#fff" stroke-width="2"/></svg></div>
    <h4>INSURANCE &amp; HEALTHCARE</h4>
    <p>Lorem Ipsum has been the industry's standard dummy text ever since the 1500s, when an unknown printer took a galley</p>
  </div>
  <div class="svc" style="left:345px">
    <div class="circle"><svg width="44" height="44" viewBox="0 0 24 24"><path d="M21 16v-2l-8-5V3.5a1.5 1.5 0 0 0-3 0V9l-8 5v2l8-2.5V19l-2 1.5V22l3.5-1 3.5 1v-1.5L13 19v-5.5z" fill="#8cc13a"/></svg></div>
    <h4>MEDICAL TOURISM</h4>
    <p>orem Ipsum has been the industry's standard dummy text ever since the 1500s, when an unknown printer took a galley</p>
  </div>
  <div class="svc" style="left:606px">
    <div class="circle"><svg width="40" height="44" viewBox="0 0 40 44"><path d="M2 2h36L22 22v16h8v4H10v-4h8V22z" fill="#8cc13a"/></svg></div>
    <h4>COST OF LIVING</h4>
    <p>orem Ipsum has been the industry's standard dummy text ever since the 1500s, when an unknown printer took a galley</p>
  </div>
  <div class="svc" style="left:876px">
    <div class="circle"><svg width="50" height="40" viewBox="0 0 50 40"><circle cx="25" cy="10" r="7" fill="#8cc13a"/><circle cx="10" cy="14" r="5.5" fill="#8cc13a"/><circle cx="40" cy="14" r="5.5" fill="#8cc13a"/><path d="M13 38c0-10 5-16 12-16s12 6 12 16z" fill="#8cc13a"/><path d="M0 36c0-8 4-13 10-13 3 0 5 1 6 3-2 3-3 6-3 10z" fill="#8cc13a"/><path d="M50 36c0-8-4-13-10-13-3 0-5 1-6 3 2 3 3 6 3 10z" fill="#8cc13a"/></svg></div>
    <h4>SUNSET HARBOR LIVING STORY</h4>
    <p>orem Ipsum has been the industry's standard dummy text ever since the 1500s, when an unknown printer took a galley</p>
  </div>
</section>

<h2 class="sec-head" style="left:90px;top:1820px">MOST POPULAR <span class="accent">PLACE</span></h2>
<svg class="pager" style="left:1081px;top:1825px" width="32" height="18" viewBox="0 0 32 18"><use href="#chev-l" stroke="#222"/><use href="#chev-r" x="20" stroke="#222"/></svg>

<article class="place" style="left:90px">
  <div class="photo" role="img" aria-label="Carved stone temple gate under a blue sky" style="background:linear-gradient(180deg,#5c9ae0,#9ab8cf 40%,#7d6a58 70%,#5a6b3a)"></div>
  <div class="cap">Ipsum quia dolor sit amet</div>
  <svg class="mini" width="42" height="9" viewBox="0 0 100 20"><use href="#star" fill="var(--star)"/><use href="#star" x="20" fill="var(--star)"/><use href="#star" x="40" fill="var(--star)"/><use href="#star" x="60" fill="var(--star)"/><use href="#star" x="80" fill="var(--star)"/></svg>
  <svg class="chev" width="14" height="24" viewBox="0 0 11 16"><use href="#chev-r" stroke="var(--link)"/></svg>
</article>
<article class="place" style="left:348px">
  <div class="photo" role="img" aria-label="Turquoise lagoon between limestone cliffs" style="background:linear-gradient(180deg,#6aa4d8,#8fb29a 40%,#3f7a56 60%,#1fa0b0)"></div>
  <div class="cap">Ipsum quia dolor sit amet</div>
  <svg class="mini" width="42" height="9" viewBox="0 0 100 20"><use href="#star" fill="var(--star)"/><use href="#star" x="20" fill="var(--star)"/><use href="#star" x="40" fill="var(--star)"/><use href="#star" x="60" fill="var(--star)"/><use href="#star" x="80" fill="var(--star)"/></svg>
  <svg class="chev" width="14" height="24" viewBox="0 0 11 16"><use href="#chev-r" stroke="var(--link)"/></svg>
</article>
<article class="place" style="left:607px">
  <div class="photo" role="img" aria-label="Red and green pagoda temple among trees" style="background:linear-gradient(180deg,#7fb0e0,#b54a3a 45%,#7a8b3a 75%,#4d6a2a)"></div>
  <div class="cap">Ipsum quia dolor sit amet</div>
  <svg class="mini" width="42" height="9" viewBox="0 0 100 20"><use href="#star" fill="var(--star)"/><use href="#star" x="20" fill="var(--star)"/><use href="#star" x="40" fill="var(--star)"/><use href="#star" x="60" fill="var(--star)"/><use href="#star" x="80" fill="var(--star)"/></svg>
  <svg class="chev" width="14" height="24" viewBox="0 0 11 16"><use href="#chev-r" stroke="var(--link)"/></svg>
</article>
<article class="place" style="left:865px">
  <div class="photo" role="img" aria-label="Golden pagodas on a hilltop with gardens" style="background:linear-gradient(180deg,#3f7fd4,#8fb1de 40%,#b78a6a 65%,#5e8b34)"></div>
  <div class="cap">Ipsum quia dolor sit amet</div>
  <svg class="mini" width="42" height="9" viewBox="0 0 100 20"><use href="#star" fill="var(--star)"/><use href="#star" x="20" fill="var(--star)"/><use href="#star" x="40" fill="var(--star)"/><use href="#star" x="60" fill="var(--star)"/><use href="#star" x="80" fill="var(--star)"/></svg>
  <svg class="chev" width="14" height="24" viewBox="0 0 11 16"><use href="#chev-r" stroke="var(--link)"/></svg>
</article>

<section class="blogs">
  <h2 class="sec-head" style="left:90px;top:51px;font-size:18px">RECENT <span class="accent">BLOGS</span></h2>
  <svg class="pager" style="left:1090px;top:55px" width="22" height="14" viewBox="0 0 32 18"><use href="#chev-l" stroke="#222"/><use href="#chev-r" x="20" stroke="#222"/></svg>
  <div class="blog-photo" style="left:92px;background:linear-gradient(180deg,#8ec5e0,#4f9a6a 45%,#2fb0b5 70%,#8a6a44)" role="img" aria-label="Longtail boat moored at a tropical beach"></div>
  <div class="blog-text" style="left:318px">
    <h4>SIMPLY DUMMY TEXT</h4>
    <div class="date">21-sep-2015</div>
    <p>Lorem Ipsum has been the industry's standard dummy text ever since the 1500s, when an unknown printer took a galley of type and scrambled it to make a type specimen book. It has survived not only five centuries, but also popularised</p>
    <a class="more" style="margin-top:6px">Read More &gt;&gt;</a>
  </div>
  <div class="blog-photo" style="left:622px;background:linear-gradient(180deg,#4a86d0,#a9c4e4 45%,#c7a25a 70%,#6a7f8f)" role="img" aria-label="Ornate golden temple under a bright sky"></div>
  <div class="blog-text" style="left:852px">
    <h4>SIMPLY DUMMY TEXT</h4>
    <div class="date">21-sep-2015</div>
    <p>Lorem Ipsum has been the industry's standard dummy text ever since the 1500s, when an unknown printer took a galley of type and scrambled it to make a type specimen book. It has survived not only five centuries, but also popularised</p>
    <a class="more" style="margin-top:6px">Read More &gt;&gt;</a>
  </div>
</section>

<footer class="footer">
  <div class="fcol" style="left:110px;width:240px">
    <h4>NEWSLETTERS SIGN UP</h4>
    <p style="margin-top:14px">Sign up for our daily email by entering your information below</p>
    <div class="email-box">Email address</div>
    <span class="sub-btn">SUBSCRIBE</span>
  </div>
  <div class="fcol" style="left:408px;width:230px">
    <h4>LATEST TWEET</h4>
    <div class="tweet"><svg width="20" height="16" viewBox="0 0 20 16"><circle cx="10" cy="8" r="7" fill="#fff"/></svg><p>Featured Workspace : Bluemill<br>snhl.to/8Rtw2Q <i>10 hours ago</i></p></div>
    <div class="tweet"><svg width="20" height="16" viewBox="0 0 20 16"><circle cx="10" cy="8" r="7" fill="#fff"/></svg><p>Featured Workspace : Bluemill<br>snhl.to/8Rtw2Q <i>10 hours ago</i></p></div>
  </div>
  <div class="fcol" style="left:705px;width:220px">
    <h4>GET IN TOUCH</h4>
    <p style="margin-top:18px">Address : 742 Lagoon Crescent,<br>Palm Bay, QLD</p>
    <p style="margin-top:14px">Phone : 07 5550 2716</p>
    <p style="margin-top:14px">Email : hello@harborliving.net</p>
  </div>
  <div class="fcol follow" style="left:985px;width:190px">
    <h4>FOLLOW US ON</h4>
    <ul style="margin-top:6px">
      <li><span class="ring"><span></span></span>Chatterly</li>
      <li><span class="ring"><span></span></span>Chirpline</li>
      <li><span class="ring"><span></span></span>Snapframe</li>
    </ul>
  </div>
</footer>
<div class="copyright">Copyright © 2016. All Rights Reserved</div>

</body>
</html>
```